New Business Card Design Project

We require a business card design for Vexalund, a newly established Indian company.
Our focus is on the development, manufacturing, and export of a diverse array of pharmaceutical products on a global scale. The card should convey a professional appearance, as our primary markets are in Africa, China, and Southeast Asian nations.
We envision a two-sided business card, with the reverse side dedicated to a logo set against a solid color or an elegantly designed pattern. The corners should be rounded. We would appreciate seeing both horizontal and vertical design options. We trust the designer to utilize their expertise in creating this design.

The content for the business card is included in the attached Word file.

Target Market(s)

Our primary markets are in Africa, China, and Southeast Asian, Latin America, Maldives, Sri Lanka

Industry/Entity Type

Pharmaceutical Manufacturing and Export

Contact Information for Business Card

Colors

Designer to choose colors to be used in the design.

Requirements
Must have
• The reverse side of the business card features solely the logo along with the tagline, "Remedies of Life."
Should not have
• The logo should not exceed two instances, encompassing both the front and back sides of the card.

```html
<!DOCTYPE html>
<html lang="en">
<head>
<meta charset="utf-8">
<title>Vexalund Business Card</title>
<link rel="stylesheet" href="https://fonts.googleapis.com/css2?family=Montserrat:wght@400;500;600;700&family=Lato:wght@400&display=swap">
<style>
  :root {
    --backdrop: #4e545c;
    --brand-blue: #27a8e0;
    --accent-red: #ef5e4a;
    --paper: #ffffff;
    --ink: #222222;
    --ink-soft: #5a5a5a;
  }
  * { margin: 0; padding: 0; box-sizing: border-box; }
  html, body {
    width: 1200px;
    height: 1120px;
    overflow: hidden;
    background: var(--backdrop);
  }
  .canvas {
    position: relative;
    width: 1200px;
    height: 1120px;
  }
  .card {
    position: absolute;
    border-radius: 27px;
    overflow: hidden;
    box-shadow: 0 14px 22px rgba(0, 0, 0, 0.35);
  }

  /* Reverse side */
  .card-back {
    left: 156px;
    top: 120px;
    width: 726px;
    height: 415px;
    background: var(--brand-blue);
  }
  .card-back .brand-dot {
    position: absolute;
    left: 133px;
    top: 64px;
    width: 44px;
    height: 44px;
    border-radius: 50%;
    background: var(--paper);
  }
  .card-back .brand-name {
    position: absolute;
    left: 36px;
    top: 148px;
    font-family: "Montserrat", sans-serif;
    font-weight: 600;
    font-size: 52px;
    line-height: 1;
    color: var(--paper);
  }
  .card-back .tagline {
    position: absolute;
    left: 229px;
    top: 358px;
    font-family: "Montserrat", sans-serif;
    font-weight: 600;
    font-size: 29px;
    line-height: 1;
    color: var(--paper);
  }

  /* Front side */
  .card-front {
    left: 323px;
    top: 607px;
    width: 701px;
    height: 401px;
    background: var(--paper);
  }
  .card-front .swoosh {
    position: absolute;
    inset: 0;
  }
  .card-front .brand-dot {
    position: absolute;
    left: 160px;
    top: 118px;
    width: 46px;
    height: 46px;
    border-radius: 50%;
    background: var(--accent-red);
  }
  .card-front .brand-name {
    position: absolute;
    left: 70px;
    top: 204px;
    font-family: "Montserrat", sans-serif;
    font-weight: 600;
    font-size: 47px;
    line-height: 1;
    color: var(--brand-blue);
  }
  .card-front .divider {
    position: absolute;
    left: 328px;
    top: 57px;
    width: 2px;
    height: 224px;
    background: linear-gradient(to bottom, rgba(39,168,224,0.2), var(--brand-blue) 40%, var(--brand-blue) 60%, rgba(39,168,224,0.2));
  }
  .person {
    position: absolute;
    left: 362px;
    top: 68px;
  }
  .person-name {
    font-family: "Montserrat", sans-serif;
    font-weight: 600;
    font-size: 25px;
    line-height: 1;
    color: var(--brand-blue);
    letter-spacing: 0.3px;
  }
  .person-role {
    margin-top: 10px;
    font-family: "Montserrat", sans-serif;
    font-weight: 400;
    font-size: 16px;
    line-height: 1;
    color: var(--ink);
  }
  .contact-list {
    position: absolute;
    left: 361px;
    top: 159px;
    list-style: none;
  }
  .contact-item {
    display: flex;
    align-items: center;
    height: 33px;
    font-family: "Lato", sans-serif;
    font-size: 13.5px;
    color: var(--ink-soft);
  }
  .contact-item svg {
    width: 20px;
    height: 20px;
    margin-right: 16px;
    flex: none;
  }
</style>
</head>
<body>
<main class="canvas">

  <section class="card card-back" aria-label="Card reverse">
    <div class="brand-dot"></div>
    <div class="brand-name">Vexalund</div>
    <div class="tagline">Remedies of Life</div>
  </section>

  <section class="card card-front" aria-label="Card front">
    <svg class="swoosh" viewBox="0 0 701 401" width="701" height="401" aria-hidden="true">
      <path d="M136 401 Q560 380 701 172 L701 401 Z" fill="var(--brand-blue)"/>
      <path d="M100 401 Q430 360 626 229" fill="none" stroke="var(--accent-red)" stroke-width="5" stroke-linecap="round"/>
    </svg>

    <div class="brand-dot"></div>
    <div class="brand-name">Vexalund</div>

    <div class="divider"></div>

    <div class="person">
      <div class="person-name">DANIEL HARTMAN</div>
      <div class="person-role">MANAGING DIRECTOR</div>
    </div>

    <ul class="contact-list">
      <li class="contact-item">
        <svg viewBox="0 0 20 20" aria-hidden="true"><path d="M10 1.5a6 6 0 0 0-6 6c0 4.5 6 11 6 11s6-6.5 6-11a6 6 0 0 0-6-6z" fill="var(--accent-red)"/><circle cx="10" cy="7.5" r="2.3" fill="#fff"/></svg>
        STREET, CITY, COUNTRY
      </li>
      <li class="contact-item">
        <svg viewBox="0 0 20 20" aria-hidden="true"><rect x="1" y="4" width="18" height="13" fill="var(--accent-red)"/><path d="M1 4 L10 11 L19 4" fill="none" stroke="#fff" stroke-width="1.4"/></svg>
        LOREMIPSUM@MAIL.COM
      </li>
      <li class="contact-item">
        <svg viewBox="0 0 20 20" aria-hidden="true"><circle cx="10" cy="10" r="8.5" fill="none" stroke="var(--accent-red)" stroke-width="1.8"/><circle cx="10" cy="10" r="5.5" fill="var(--accent-red)"/><path d="M10 1.5v17M1.5 10h17" stroke="#fff" stroke-width="1.2"/></svg>
        WWW.LOREM IPSUM.COM
      </li>
      <li class="contact-item">
        <svg viewBox="0 0 20 20" aria-hidden="true"><path d="M4 2 L7.5 2 L8.5 6.5 L6.3 8 C7.3 10.5 9.5 12.7 12 13.7 L13.5 11.5 L18 12.5 L18 16 C18 17.2 17 18 15.8 18 C8.5 17.5 2.5 11.5 2 4.2 C2 3 2.8 2 4 2z" fill="var(--accent-red)"/></svg>
        01 8000 00 00
      </li>
    </ul>
  </section>

</main>
</body>
</html>
```